Business Card Design Project

We are not a new company, but renamed to "Vantorin Kitchens" last year. We specialize in modern high-end cabinetry imports. We would like to communicate a sense of quality and cutting edge technology. Ideally the design would incorporate our logo colors, silver, red and preferably a black, matte background. Though we are open to suggestions.
Logo is attached.
Edit: I have attached rough drafts of the previous cards, this way you will have all necessary content that needs to go on the cards.
Updates
Project Deadline Extended
Reason: We have received a lot of great designs, but due to the sheer number we couldn't respond to all. We will extend the deadline for another 7 days to finalize and provide feedback to designers.
Thank you for your hard work!
Industry/Entity Type
Business
Look and feel
Each slider illustrates characteristics of the customer's brand and the style your logo design should communicate.

```html
<!DOCTYPE html>
<html lang="en">
<head>
<meta charset="utf-8">
<title>Vantorin Kitchens — Business Cards</title>
<link rel="stylesheet" href="https://fonts.googleapis.com/css2?family=Arimo:wght@400;700&display=swap">
<style>
  :root {
    --stage: #7a4e2c;
    --label: #2a1a0e;
    --card-black: #1a1b1d;
    --card-charcoal: #2b2d30;
    --ink-white: #ffffff;
    --ink-dark: #1d1d1f;
    --silver: #c4c6c9;
    --silver-light: #e9eaeb;
    --silver-mid: #b7b9bc;
    --brand-red: #e31b23;
  }
  * { box-sizing: border-box; margin: 0; padding: 0; }
  html, body { width: 1200px; height: 788px; overflow: hidden; }
  body {
    position: relative;
    background: var(--stage);
    font-family: "Arimo", Arial, sans-serif;
  }
  .side-label {
    position: absolute;
    font-size: 21px;
    color: var(--label);
    transform: translateX(-50%);
  }
  .card {
    position: absolute;
    width: 524px;
    height: 299px;
    border-radius: 22px;
    overflow: hidden;
    background: radial-gradient(ellipse at 50% 40%, var(--card-charcoal), var(--card-black) 75%);
    box-shadow: 0 6px 14px rgba(0,0,0,.45);
  }
  .card--front { top: 72px; left: 54px; }
  .card--front-alt { top: 72px; left: 619px; }
  .card--back { top: 447px; left: 56px; }
  .card--back-alt { top: 447px; left: 625px; background: #0d0d0e; }
  .swoosh { position: absolute; inset: 0; width: 100%; height: 100%; }
  .brand-name {
    position: absolute;
    font-weight: 700;
    text-transform: uppercase;
    color: var(--silver);
    white-space: nowrap;
    display: flex;
    align-items: center;
    gap: 10px;
  }
  .brand-name::before {
    content: "";
    width: 14px; height: 14px;
    background: var(--brand-red);
  }
  .card--front .brand-name,
  .card--front-alt .brand-name { top: 86px; left: 29px; font-size: 24px; letter-spacing: 1px; }
  .card--back .brand-name,
  .card--back-alt .brand-name { top: 152px; left: 50%; transform: translateX(-50%); font-size: 30px; letter-spacing: 1.5px; }
  .contact { position: absolute; top: 140px; left: 29px; color: var(--ink-white); }
  .contact__name { font-size: 16px; margin-bottom: 13px; }
  .contact__name strong { font-weight: 700; }
  .contact__title { font-size: 15px; }
  .card--front-alt .contact__name { font-weight: 400; }
  .card--front-alt .contact__title { font-size: 13px; }
  .contact__line { font-size: 13px; line-height: 20.5px; }
  .contact__line b { font-weight: 700; }
  .contact__email { font-size: 13px; margin-top: 8px; }
  .address {
    position: absolute;
    right: 30px; bottom: 12px;
    text-align: right;
    font-size: 13px;
    line-height: 19px;
    color: var(--ink-dark);
  }
  .texture-area { position: absolute; }
  .texture-area--top { top: 0; left: 0; width: 290px; height: 110px;
    background: radial-gradient(ellipse at 45% 30%, #6a6b6e, #2a2b2d 55%, transparent 80%); }
  .texture-area--bottom { right: 0; bottom: 0; width: 260px; height: 110px;
    background: radial-gradient(ellipse at 50% 65%, #6a6b6e, #2a2b2d 55%, transparent 80%); }
</style>
</head>
<body>

  <span class="side-label" style="left:307px; top:24px;">front</span>
  <span class="side-label" style="left:889px; top:24px;">front-1</span>
  <span class="side-label" style="left:314px; top:406px;">back</span>
  <span class="side-label" style="left:893px; top:406px;">Back - 1</span>

  <!-- Front: President -->
  <section class="card card--front">
    <svg class="swoosh" viewBox="0 0 524 299" preserveAspectRatio="none" aria-hidden="true">
      <defs>
        <linearGradient id="silverFill" x1="0" y1="0" x2="1" y2="1">
          <stop offset="0" stop-color="var(--silver-light)"/>
          <stop offset="1" stop-color="var(--silver-mid)"/>
        </linearGradient>
      </defs>
      <path d="M0,272 C150,300 380,232 524,160 L524,299 L0,299 Z" fill="url(#silverFill)"/>
      <path d="M0,262 C160,290 370,190 524,112 L524,150 C380,222 160,292 0,268 Z" fill="var(--brand-red)"/>
      <path d="M0,270 C160,298 380,226 524,154" fill="none" stroke="#000" stroke-width="3"/>
    </svg>
    <div class="brand-name">Vantorin Kitchens</div>
    <div class="contact">
      <p class="contact__name"><strong>MIREK DALTON,</strong> <span class="contact__title">President</span></p>
      <p class="contact__line"><b>phone</b> : 555.210.0147</p>
      <p class="contact__line"><b>cell</b> : 555.318.2296</p>
      <p class="contact__line"><b>fax</b> : 555.210.0152</p>
      <p class="contact__email">mirek@vantorinkitchens.ca</p>
    </div>
    <address class="address" style="font-style:normal;">2180 - 47 St.<br>Calgary, AB T2K 4R8</address>
  </section>

  <!-- Front: Director -->
  <section class="card card--front-alt">
    <svg class="swoosh" viewBox="0 0 524 299" preserveAspectRatio="none" aria-hidden="true">
      <path d="M0,272 C150,300 380,232 524,160 L524,299 L0,299 Z" fill="url(#silverFill)"/>
      <path d="M0,262 C160,290 370,190 524,112 L524,150 C380,222 160,292 0,268 Z" fill="var(--brand-red)"/>
      <path d="M0,270 C160,298 380,226 524,154" fill="none" stroke="#000" stroke-width="3"/>
    </svg>
    <div class="brand-name">Vantorin Kitchens</div>
    <div class="contact">
      <p class="contact__name">TOMAS DALTON, <span class="contact__title">Director</span></p>
      <p class="contact__line"><b>phone</b> : 555.210.0147</p>
      <p class="contact__line"><b>cell</b> : 555.406.7731</p>
      <p class="contact__line"><b>fax</b> : 555.210.0152</p>
      <p class="contact__email">tomas@vantorinkitchens.ca</p>
    </div>
    <address class="address" style="font-style:normal;">2180 - 47 St.<br>Calgary, AB T2K 4R8</address>
  </section>

  <!-- Back -->
  <section class="card card--back">
    <div class="brand-name">Vantorin Kitchens</div>
  </section>

  <!-- Back alternative -->
  <section class="card card--back-alt">
    <div class="texture-area texture-area--top" role="img" aria-label="Perforated metal texture, top left corner"></div>
    <div class="texture-area texture-area--bottom" role="img" aria-label="Perforated metal texture, bottom right corner"></div>
    <div class="brand-name">Vantorin Kitchens</div>
  </section>

</body>
</html>
```